Business Cards for Volmont Hayes, a law firm

We changed our firm's name from "Volmont & Hayes LLP" to "Volmont Hayes", we need to update our cards with a new design. We like the overall look of the back but the front side of the cards (see attached mockup) needs a refreshed look. I also attach our current logo so you can get rid of that LLP and &. We have a new address as well (not same as on mockup).

Target Market(s)

Clients of law firm

Industry/Entity Type

Law Firm

Contact Information for Business Card

Frontsides:

Lorenzo T. Volmont
Partner
Tel: (416) 555-0172 ext. 101
Fax: (647) 555-0139
Email: lvolmont@vhlegal.example

Simon P. Hayes
Partner
Tel: (416) 555-0172 ext. 102
Fax: (647) 555-0139
Email: simonhayes@vhlegal.example

Mark E. Dorsan
Barrister
Tel: (416) 555-0172 ext. 104
Fax: (647) 555-0139
Email: mdorsan@vhlegal.example

The back side should be crimson red (see mockup) with the logo (please update it to remove the & and the LLP, you can modify it a bit to make it tasteful if need be). Our new address is

82 Marlow Rd W, Suite 710
Toronto, ON M5K 0Z9

After our address, please also include our website www.vhlegal.example

Font styles to use
Sans Serif

Colors
ec2027
ffffff
000000

Requirements
Must have
• PLEASE NOTE: our firm's colour is more of a darker/crimson red, not a vibrant red.
• The front should have space for the lawyer's name, title, phone number (with extension), fax number, and email.
• If you're going to add those yourself, the info for the frontside is in the "Business Card Details" section (three lawyers that need their own cards).
Nice to have
• We like the backside of our current cards, just update it with our new address (one address now instead of 2), and a slightly modified logo (not a new logo altogether).
• The frontside should be refreshed with a better look (think minimalist, professional and modern), although still predominantly white-based background.
Should not have
• No scales of justice or other cheesy lawyer stereotype symbols! :-)

```html
<!DOCTYPE html>
<html lang="en">
<head>
<meta charset="utf-8">
<title>Volmont Hayes – Business Card Back</title>
<link rel="stylesheet" href="https://fonts.googleapis.com/css2?family=Barlow:wght@500;700&display=swap">
<style>
  :root {
    --stage: #f3f3f3;
    --card-red: #e4403c;
    --ink-white: #ffffff;
    --ink-black: #111111;
    --guide: #b9b9b9;
  }
  html, body {
    margin: 0;
    padding: 0;
    overflow: hidden;
  }
  .canvas {
    position: relative;
    width: 1200px;
    height: 652px;
    background: var(--stage);
    overflow: hidden;
    font-family: "Barlow", Arial, sans-serif;
  }
  .trim-guides {
    position: absolute;
    inset: 0;
    width: 1200px;
    height: 652px;
  }
  .card-back {
    position: absolute;
    left: 23px;
    top: 48px;
    width: 1151px;
    height: 574px;
    background: var(--card-red);
  }
  .brand {
    position: absolute;
    left: 0;
    right: 0;
    top: 64px;
    display: flex;
    flex-direction: column;
    align-items: center;
  }
  .brand-dot {
    width: 172px;
    height: 172px;
    border-radius: 50%;
    background: var(--ink-black);
  }
  .brand-name {
    margin: 42px 0 0;
    font-weight: 700;
    font-size: 64px;
    line-height: 1;
    letter-spacing: 0.5px;
    color: var(--ink-white);
  }
  .divider {
    position: absolute;
    left: 0;
    right: 0;
    top: 412px;
    height: 2px;
    background: var(--ink-black);
  }
  .address {
    position: absolute;
    left: 48px;
    top: 456px;
    margin: 0;
    font-style: normal;
    font-weight: 500;
    font-size: 24px;
    line-height: 35px;
    color: var(--ink-white);
  }
  .website {
    position: absolute;
    right: 95px;
    top: 471px;
    margin: 0;
    font-weight: 500;
    font-size: 24px;
    line-height: 35px;
    letter-spacing: 0.8px;
    color: var(--ink-white);
  }
</style>
</head>
<body>
<main class="canvas">
  <section class="card-back" aria-label="Business card back">
    <div class="brand">
      <div class="brand-dot" aria-hidden="true"></div>
      <h1 class="brand-name">Volmont Hayes</h1>
    </div>
    <div class="divider" aria-hidden="true"></div>
    <address class="address">82 Marlow Rd W, Suite 710<br>Toronto, ON M5K 0Z9</address>
    <p class="website">www.vhlegal.example</p>
  </section>
  <svg class="trim-guides" viewBox="0 0 1200 652" aria-hidden="true">
    <g stroke="var(--guide)" stroke-width="1.5" stroke-dasharray="6 5" fill="none">
      <line x1="786" y1="0" x2="1200" y2="306"/>
      <line x1="1200" y1="350" x2="815" y2="652"/>
    </g>
  </svg>
</main>
</body>
</html>
```